Oriel Photography Business Card

I need a business card designed for a photography business based in Perth, Western Australia called Oriel Photography.

We specialise in wedding, event photography and portrait photography.

The business card must borrow the style of the attached logo.

The hex codes for the colours in the logo are:
#ED1D85 - Pink
#89C23E - Green
#37282F - Black

The name on the card will be:
Name: Tobrian
Phone: 0417395268
Website: www.orielphotography.example.com.au
Facebook: orielphotography

I am open and happy to accept creative concepts.

I’d like some space at the back for writing notes and appointment details.

```html
<!DOCTYPE html>
<html lang="en">
<head>
<meta charset="utf-8">
<title>Oriel Photography – Business Card</title>
<link href="https://fonts.googleapis.com/css2?family=Open+Sans:ital,wght@0,400;0,600;0,700;1,400&family=Cinzel:wght@400&display=swap" rel="stylesheet">
<style>
  :root{
    --pink:#ED1D85;
    --green:#89C23E;
    --black:#37282F;
    --grey:#5a5458;
    --line:#9a9a9a;
    --paper:#ffffff;
    --backdrop:#e6e6ec;
  }
  *{box-sizing:border-box;margin:0;padding:0}
  html,body{width:1200px;height:987px;overflow:hidden}
  body{background:var(--backdrop);font-family:"Open Sans",Arial,sans-serif;position:relative}

  .card{position:absolute;top:328px;width:540px;height:330px;background:var(--paper);
        border-radius:26px;overflow:hidden;box-shadow:0 6px 18px rgba(0,0,0,.12)}
  .card--front{left:36px}
  .card--back{left:624px}

  /* front */
  .front-sweep{position:absolute;inset:0}
  .brand-mark{position:absolute;left:246px;top:34px;width:56px;height:56px;border-radius:50%;
              background:var(--green)}
  .brand-wordmark{position:absolute;left:0;right:0;top:104px;text-align:center;
                  font-size:17px;letter-spacing:9px;color:var(--grey);font-weight:400;text-transform:uppercase}
  .person-name{position:absolute;left:0;right:0;top:136px;text-align:center;
               font-size:24px;font-weight:700;color:var(--pink);letter-spacing:1px;text-transform:uppercase}
  .contact{position:absolute;left:30px;color:#fff;font-size:15px;display:flex;align-items:center;gap:7px}
  .contact--phone{top:236px}
  .contact--web{top:268px}
  .contact svg{flex:none}
  .social-square{width:13px;height:13px;background:#fff;margin-left:10px}

  /* back */
  .appt-title{position:absolute;left:30px;top:24px;font-family:"Cinzel",Georgia,serif;
              color:var(--pink);font-size:19px;letter-spacing:1px}
  .form-row{position:absolute;left:30px;display:flex;align-items:flex-end;gap:8px;
            font-size:14px;color:var(--grey)}
  .rule{border-bottom:1px dotted var(--line);height:1px;margin-bottom:4px}
  .box{border:1px solid var(--line);border-radius:3px;height:26px}
  .days{position:absolute;left:30px;top:204px;display:flex;gap:9px;align-items:center;
        font-size:13px;font-weight:700;color:var(--grey)}
  .days .box{width:28px;height:22px;margin-right:4px}
  .note{position:absolute;left:30px;top:246px;font-style:italic;font-size:13px;color:var(--grey)}
  .back-brand{position:absolute;right:26px;top:270px;display:flex;align-items:center;gap:8px;
              color:var(--pink);font-size:14px;font-weight:600}
  .back-brand .dot{width:22px;height:22px;border-radius:50%;background:var(--green)}
</style>
</head>
<body>

<section class="card card--front" aria-label="Card front">
  <svg class="front-sweep" width="540" height="330" viewBox="0 0 540 330" aria-hidden="true">
    <path d="M0,170 Q270,190 470,330 L0,330 Z" fill="var(--pink)"/>
    <path d="M0,158 Q285,176 492,330" fill="none" stroke="var(--black)" stroke-width="3"/>
  </svg>
  <div class="brand-mark" aria-hidden="true"></div>
  <div class="brand-wordmark">Oriel Photography</div>
  <div class="person-name">Tobrian</div>
  <div class="contact contact--phone">
    <svg width="14" height="14" viewBox="0 0 24 24" aria-hidden="true"><path fill="#fff" d="M6.6 10.8a15 15 0 0 0 6.6 6.6l2.2-2.2c.3-.3.7-.4 1-.2 1.1.4 2.3.6 3.6.6.6 0 1 .4 1 1V20c0 .6-.4 1-1 1A17 17 0 0 1 3 4c0-.6.4-1 1-1h3.5c.6 0 1 .4 1 1 0 1.3.2 2.5.6 3.6.1.3 0 .7-.2 1z"/></svg>
    <span>0417395268</span>
    <span class="social-square" aria-hidden="true"></span>
    <span>orielphotography</span>
  </div>
  <div class="contact contact--web">
    <svg width="14" height="14" viewBox="0 0 24 24" aria-hidden="true" fill="none" stroke="#fff" stroke-width="2"><circle cx="12" cy="12" r="10"/><path d="M2 12h20M12 2c3 3 3 17 0 20M12 2c-3 3-3 17 0 20"/></svg>
    <span>www.orielphotography.example.com.au</span>
  </div>
</section>

<section class="card card--back" aria-label="Card back">
  <h2 class="appt-title">YOUR APPOINTMENT</h2>
  <div class="form-row" style="top:62px"><span>Name :</span><span class="rule" style="width:410px"></span></div>
  <div class="form-row" style="top:92px"><span>Date :</span><span class="rule" style="width:160px"></span>
    <span>Time :</span><span class="rule" style="width:190px"></span></div>
  <div class="form-row" style="top:130px"><span>Next Appointment</span><span class="box" style="width:120px"></span>
    <span class="box" style="width:130px"></span><span>am / pm</span></div>
  <div class="days">
    <span>MON</span><span class="box"></span>
    <span>TUE</span><span class="box"></span>
    <span>WED</span><span class="box"></span>
    <span>THU</span><span class="box"></span>
    <span>FRI</span><span class="box"></span>
    <span>SAT</span><span class="box"></span>
  </div>
  <p class="note">We appreciate a 24 hr. notice for cancellations</p>
  <div class="back-brand"><span class="dot" aria-hidden="true"></span><span>Oriel Photography</span></div>
</section>

</body>
</html>
```